Red Mo's Wine Label Project

We need a new entry level wine label called "Red Mo's" for a range of wines we are developing from inland Australia. Our company is made up of three youngish guys who live hard and love taking the mickey. Red Mo is Red Morrie - the largest and loudest of the three partners (and ideally this label will take the mickey out of him). We've grown the grapes ourselves for this first release which will be a 2012 Pinot Gris. Wine style is dry, young, fresh and contemporary and pitched at the sub AUD $10 retail price point. The package will be flint (clear) claret shape bottle with plain screwcap (colour matched to suit the winning label design).

I've attached a couple of photos of Red Morrie to give you some idea of his presence and persona.

Target Market(s)

Semi educated 25 - 40 year old wine drinkers. Skewed towards females.

Industry/Entity Type

Retail

Requirements
Should not have
• Anything traditional or old fashioned

```html
<!DOCTYPE html>
<html lang="en">
<head>
<meta charset="utf-8">
<title>Red Mo's Pinot Gris Label</title>
<link href="https://fonts.googleapis.com/css2?family=Bebas+Neue&family=Josefin+Sans:wght@300;400&display=swap" rel="stylesheet">
<style>
  :root {
    --page: #f3f3f1;
    --label-edge: #cfd1cf;
    --label-centre: #ffffff;
    --ink: #1c1c1c;
    --band-green: #4b8b3b;
    --band-text: #f4f8f0;
    --press-dark: #4a4a48;
    --press-light: #b9b9b4;
  }
  html, body {
    margin: 0;
    padding: 0;
  }
  body {
    width: 1200px;
    height: 4041px;
    overflow: hidden;
    background: var(--page);
    display: flex;
    align-items: center;
    justify-content: center;
  }
  .wine-label {
    width: 1000px;
    height: 880px;
    display: flex;
    flex-direction: column;
    background: linear-gradient(90deg, var(--label-edge) 0%, var(--label-centre) 22%, var(--label-centre) 78%, var(--label-edge) 100%);
    box-shadow: 0 2px 10px rgba(0,0,0,0.08);
  }
  .label-masthead {
    height: 656px;
    display: flex;
    align-items: center;
    justify-content: center;
    gap: 34px;
    padding: 0 40px;
    box-sizing: border-box;
  }
  .brand-name {
    margin: 0;
    font-family: 'Bebas Neue', 'Oswald', sans-serif;
    font-weight: 400;
    font-size: 290px;
    line-height: 1;
    color: var(--ink);
    letter-spacing: 2px;
    padding-top: 60px;
  }
  .press-illustration {
    width: 270px;
    height: 330px;
    margin-top: 20px;
    border-radius: 6px;
    background: radial-gradient(ellipse at 50% 45%, var(--press-light) 0%, var(--press-dark) 85%);
  }
  .details-band {
    height: 86px;
    background: var(--band-green);
    display: flex;
    align-items: center;
    padding-left: 14px;
  }
  .details-band p {
    margin: 0;
    font-family: 'Josefin Sans', sans-serif;
    font-weight: 300;
    font-size: 33px;
    letter-spacing: 2px;
    color: var(--band-text);
    text-transform: uppercase;
    white-space: nowrap;
  }
  .details-band .divider {
    margin: 0 14px;
  }
  .label-foot {
    flex: 1;
  }
</style>
</head>
<body>
  <main class="wine-label">
    <section class="label-masthead">
      <h1 class="brand-name">Red Mo</h1>
      <div class="press-illustration" role="img" aria-label="Engraved illustration of a traditional wooden wine press with screw and standing legs"></div>
    </section>
    <section class="details-band">
      <p>Pinot Gris<span class="divider">|</span>2012<span class="divider">|</span>Alkohol 12%</p>
    </section>
    <div class="label-foot"></div>
  </main>
</body>
</html>
```